Tolbek cards

I want a simple business card that pops.
Logo on one side.
On side two i want.
"Are you thinking about a new building on your property, or renovating an existing structure? Contact".....
Owners Name: Dale Whitacre
Owners Phone number: 610-555-0187
Address:4076 Copper Ridge RD, Alder Falls, PA 16990
Committed to Quality, Service, and Integrity

```html
<!DOCTYPE html>
<html lang="en">
<head>
<meta charset="utf-8">
<title>Tolbek Builders LLC – Business Card</title>
<link rel="stylesheet" href="https://fonts.googleapis.com/css2?family=Archivo:wght@400;600;700;800&display=swap">
<style>
  :root {
    --page-bg: #2b2b2b;
    --card-bg: #f1f0ee;
    --brown-dark: #4a3322;
    --brown-tan: #8c7356;
    --band-light: #9a8266;
    --band-dark: #5e4632;
    --rule: #b9a78f;
    --text-dark: #2f2419;
    --text-light: #f4efe8;
  }
  * { margin: 0; padding: 0; box-sizing: border-box; }
  html, body {
    width: 1200px; height: 576px; overflow: hidden;
    background: var(--page-bg);
    font-family: "Archivo", Arial, sans-serif;
  }
  .canvas { position: relative; width: 1200px; height: 576px; }

  .card {
    position: absolute; top: 139px;
    width: 484px; height: 292px;
    background: var(--card-bg);
    border-radius: 10px;
    overflow: hidden;
  }
  .card--front { left: 102px; }
  .card--back { left: 596px; width: 480px; }

  .brand {
    position: absolute; left: 0; right: 0;
    display: flex; align-items: center; justify-content: center; gap: 12px;
    color: var(--brown-dark);
    font-weight: 800;
    text-transform: uppercase;
    white-space: nowrap;
  }
  .brand__square { background: var(--brown-dark); flex: none; }
  .card--front .brand { top: 110px; font-size: 31px; letter-spacing: 0.5px; }
  .card--front .brand__square { width: 28px; height: 28px; }
  .card--back .brand { top: 36px; font-size: 27px; letter-spacing: 0.5px; }
  .card--back .brand__square { width: 24px; height: 24px; }

  .tagline-band {
    position: absolute; left: 0; right: 0; bottom: 0; height: 30px;
    background: linear-gradient(90deg, var(--band-light), var(--band-dark));
    color: var(--text-light);
    font-size: 12.5px;
    display: flex; align-items: center; justify-content: center;
  }

  .pitch-band {
    position: absolute; left: 0; right: 0; top: 100px; height: 54px;
    background: var(--brown-dark);
    color: var(--text-light);
    font-size: 12.5px; font-weight: 700; line-height: 16px;
    text-transform: uppercase; text-align: center;
    padding-top: 8px;
  }
  .contact-pill {
    position: absolute; top: 146px; left: 50%; transform: translateX(-50%);
    width: 97px; height: 17px; border-radius: 9px;
    background: var(--brown-tan);
    color: var(--text-light);
    font-size: 12px; font-weight: 600; text-transform: uppercase;
    display: flex; align-items: center; justify-content: center;
  }
  .owner {
    position: absolute; top: 170px; left: 0; right: 0; text-align: center;
    font-size: 19px; font-weight: 700; text-transform: uppercase;
    color: var(--text-dark);
  }
  .owner__last { color: var(--brown-tan); }
  .phone {
    position: absolute; top: 198px; left: 0; right: 0; text-align: center;
    font-size: 12.5px; font-weight: 700; color: var(--text-dark);
  }
  .address {
    position: absolute; top: 217px; left: 0; right: 0; text-align: center;
    font-size: 11.5px; color: var(--brown-tan);
  }
  .divider {
    position: absolute; top: 243px; left: 42px; right: 40px;
    height: 1px; background: var(--rule);
  }
  .tagline {
    position: absolute; top: 254px; left: 0; right: 0; text-align: center;
    font-size: 12.5px; color: var(--text-dark);
  }
</style>
</head>
<body>
<main class="canvas">
  <section class="card card--front" aria-label="Card front">
    <div class="brand"><span class="brand__square"></span><span>Tolbek Builders LLC</span></div>
    <div class="tagline-band">Committed to Quality, Service &amp; Integrity</div>
  </section>

  <section class="card card--back" aria-label="Card back">
    <div class="brand"><span class="brand__square"></span><span>Tolbek Builders LLC</span></div>
    <div class="pitch-band">Are you thinking about a new building on your<br>property, or renovating an existing structure?</div>
    <div class="contact-pill">Contact</div>
    <div class="owner">Dale <span class="owner__last">Whitacre</span></div>
    <div class="phone">Call: 610-555-0187</div>
    <div class="address">Add.: 4076 Copper Ridge RD, Alder Falls, PA 16990</div>
    <div class="divider"></div>
    <div class="tagline">Committed to Quality, Service &amp; Integrity</div>
  </section>
</main>
</body>
</html>
```